Maple Roster Business Card for recruitment company

We are looking for a Business Card Design that incorporates our personal details and our busines name and logo. We are a specialized search consultancy that recruit Property and Construction professionals.
We would like a business card that stands out and is appealing to the Construction and Property industry as well.

Target Market(s)

people in the construction and property industry

Contact Information for Business Card

Business Name and logo

Font styles to use
Serif

Colors
0094D4
00A9DD
6FCCEA
C7EBF8
E9F6FB

Requirements
Must have
• Business name and logo as well as contact details
Should not have
• No photos of us please

```html
<!DOCTYPE html>
<html lang="en">
<head>
<meta charset="utf-8">
<title>Maple Roster – Business Card</title>
<link rel="stylesheet" href="https://fonts.googleapis.com/css2?family=Montserrat:wght@300;500;600;700&display=swap">
<style>
  :root {
    --stage: #2b3138;
    --card-white: #fafafa;
    --card-black: #151515;
    --pattern-dark: #1f1f1f;
    --ink: #1b1b1b;
    --navy: #1d3b4f;
    --orange: #f07f1e;
    --rule: #2a2a2a;
  }
  * { box-sizing: border-box; margin: 0; padding: 0; }
  html, body { width: 1200px; height: 780px; overflow: hidden; }
  body {
    background: var(--stage);
    font-family: "Montserrat", sans-serif;
    position: relative;
  }
  .card {
    position: absolute;
    top: 92px;
    width: 340px;
    height: 596px;
    border-radius: 18px;
    box-shadow: 0 18px 40px rgba(0,0,0,.45);
    overflow: hidden;
  }
  .card--front { left: 200px; background: var(--card-white); color: var(--ink); text-align: center; }
  .card--back { left: 660px; background: var(--card-black); }

  .brand {
    margin-top: 92px;
    font-weight: 300;
    font-size: 27px;
    letter-spacing: 1px;
    color: var(--navy);
    text-transform: uppercase;
  }
  .person__name {
    margin-top: 40px;
    font-weight: 700;
    font-size: 29px;
    letter-spacing: 2px;
    color: var(--orange);
  }
  .person__title {
    margin-top: 2px;
    font-weight: 500;
    font-size: 15px;
    letter-spacing: 2px;
  }
  .divider-icons {
    display: flex;
    align-items: center;
    gap: 8px;
    margin: 14px 28px 0;
  }
  .divider-icons__rule { flex: 1; height: 1px; background: var(--rule); }
  .icon {
    width: 22px; height: 22px;
    border-radius: 6px;
    background: var(--orange);
    display: flex; align-items: center; justify-content: center;
  }
  .contact {
    margin-top: 30px;
    list-style: none;
    font-weight: 600;
    font-size: 15.5px;
    letter-spacing: 1.4px;
    line-height: 1.5;
  }
  .rule { height: 1px; background: var(--rule); margin: 28px 28px 0; }
  .address {
    margin-top: 30px;
    font-style: normal;
    font-weight: 600;
    font-size: 16px;
    letter-spacing: 1.6px;
    line-height: 1.4;
  }

  .back__pattern {
    position: absolute; inset: 0;
    background: radial-gradient(circle at 50% 55%, var(--pattern-dark), var(--card-black) 75%);
  }
  .back__brand {
    position: absolute;
    left: 0; right: 0; top: 390px;
    text-align: center;
    font-weight: 600;
    font-size: 18px;
    letter-spacing: 1px;
    color: var(--orange);
  }
</style>
</head>
<body>
  <section class="card card--front" aria-label="Business card front">
    <p class="brand">Maple Roster</p>
    <h1 class="person__name">Darius Okafor</h1>
    <p class="person__title">General Manager</p>
    <div class="divider-icons">
      <span class="divider-icons__rule"></span>
      <span class="icon" aria-label="Website">
        <svg width="14" height="14" viewBox="0 0 14 14" fill="none" stroke="#fff" stroke-width="1.2">
          <circle cx="7" cy="7" r="5.5"/><ellipse cx="7" cy="7" rx="2.4" ry="5.5"/><line x1="1.5" y1="7" x2="12.5" y2="7"/>
        </svg>
      </span>
      <span class="icon" aria-label="Email">
        <svg width="14" height="14" viewBox="0 0 14 14" fill="none" stroke="#fff" stroke-width="1.2">
          <rect x="1.5" y="3" width="11" height="8" rx="1"/><polyline points="1.5,3.5 7,8 12.5,3.5"/>
        </svg>
      </span>
      <span class="icon" aria-label="Phone">
        <svg width="14" height="14" viewBox="0 0 14 14" fill="#fff">
          <path d="M3.2 1.5l2 .3.9 2.6-1.3 1a7 7 0 0 0 3.8 3.8l1-1.3 2.6.9.3 2c-.2.7-.9 1.2-1.7 1.2C5.6 12 2 8.4 2 3.2c0-.8.5-1.5 1.2-1.7z"/>
        </svg>
      </span>
      <span class="divider-icons__rule"></span>
    </div>
    <ul class="contact">
      <li>043-555-0187</li>
      <li>hello@mapleroster.com</li>
      <li>www.mapleroster.com</li>
    </ul>
    <div class="rule"></div>
    <address class="address">4820 Cedar Hollow Lane<br>Aldbury, VA 20411</address>
  </section>

  <section class="card card--back" aria-label="Business card back">
    <div class="back__pattern" role="img" aria-label="Dark repeating brand pattern"></div>
    <p class="back__brand">Maple Roster</p>
  </section>
</body>
</html>
```